Broschüren-Design für Unternehmen, das die Begrünung von Bürogebäuden anbietet
Wir sind mit der Zusammenarbeit mit inkmolde äußerst zufrieden. Vielen Dank für das ganze Mitdenken und die wichtigen Rückfragen an uns (Format, Layout, Farben, Papierwahl)! :)
Zielgruppe
Unser Kerngeschäft besteht in der Begrünung von Bürogebäuden.
Das heißt, wir liefern und pflegen exotische und tropische immergrüne Planzen für zum Beispiel Eingangsbereiche, Atrien, sowie Einzel- und Großraumbüros.
Die Zielgruppe besteht fast ausschließlich aus gewerblichen Kunden.
Aufgabenstellung
Die Vorlage ist ein grober Entwurf und Vorschlag von uns. Es darf davon auch gerne abgewichen werden.
Die Broschüre soll uns als Unterstützung für Erstgespräche bei potentiellen Neukunden dienen und verbleibt beim Kunden. Sie soll unsere Firma, uns als Menschen und unsere Produkte und Dienstleistung kurz präsentieren und einen guten Eindruck hinterlassen.
Danach wünschen wir uns idealerweise eine Kontaktaufnahme durch den Kunden selbst.

```html
<!DOCTYPE html>
<html lang="de">
<head>
<meta charset="utf-8">
<title>Wettberg Raumbegrünung – Broschüre</title>
<link rel="stylesheet" href="https://fonts.googleapis.com/css2?family=Fira+Sans:wght@500;600&family=Open+Sans:ital,wght@0,600;1,400;1,600&display=swap">
<style>
  :root{
    --stage:#b4b4b4;
    --paper:#ffffff;
    --green:#52a13f;
    --green-dark:#3a7a35;
    --green-pale:#cfe3c4;
    --green-mist:#a9cf9a;
    --anthracite:#2b2a2d;
    --ink:#1d1d1b;
    --foliage:#4e7a3a;
    --portrait:#c7c9cc;
  }
  *{box-sizing:border-box;margin:0;padding:0}
  html,body{width:1200px;height:649px;overflow:hidden;background:var(--stage)}
  body{position:relative;font-family:"Open Sans",Arial,sans-serif;color:var(--ink)}
  .spread{position:absolute;width:594px;height:210px;background:var(--paper);overflow:hidden}
  .spread--cover{width:296px}
  .shapes{position:absolute;inset:0;width:100%;height:100%}
  .heading{position:absolute;left:10px;top:14px;font-family:"Fira Sans",Arial,sans-serif;font-weight:600;font-size:9.5px;line-height:1.15;color:var(--paper)}
  .heading--green{color:var(--green)}
  .heading--small{font-size:3.6px;top:11px;font-weight:500}
  .copy{position:absolute;font-style:italic;font-size:4.1px;line-height:1.55}
  .copy p+p{margin-top:4px}
  .copy--light{color:var(--paper)}
  .copy--justify{text-align:justify}
  .copy--center{text-align:center}
  .slant-left{float:left;width:100px;height:100px;shape-outside:polygon(0 0,70px 0,24px 100px,0 100px)}
  .slant-right{float:right;width:86px;height:100px;shape-outside:polygon(45px 0,86px 0,86px 100px,0 100px)}
  .caption{position:absolute;font-size:3.6px;font-weight:600}
  .folio{position:absolute;bottom:5px;font-size:3.2px}
  .photo{position:absolute}
  .brand{position:absolute;left:222px;top:181px;display:flex;align-items:center;gap:4px;font-family:"Fira Sans",Arial,sans-serif;font-weight:500;font-size:7px;line-height:1.05;color:var(--green-dark)}
  .brand__mark{width:14px;height:14px;border:1.4px solid var(--green-dark)}
  .toc{position:absolute;font-family:"Open Sans",Arial,sans-serif;font-weight:600;font-size:4px;display:flex;align-items:baseline;height:6px}
  .toc span{white-space:nowrap;flex-shrink:0}
  .toc .toc__dots{flex:1 1 auto;flex-shrink:1;min-width:0;margin:0 1.5px;border-bottom:0.8px dotted var(--ink);transform:translateY(-1px)}
  .member{position:absolute;width:76px}
  .member__photo{width:76px;height:76px;border-radius:5px;background:var(--portrait)}
  .member__name{margin-top:3px;text-align:center;font-weight:600;font-size:5.2px;color:var(--paper)}
  .badge{position:absolute;left:470px;top:162px;width:106px;height:32px;border:1.5px solid var(--green);border-radius:3px;background:var(--paper)}
  .fold{position:absolute;top:0;bottom:0;left:297px;width:0.5px;background:rgba(0,0,0,.12)}
</style>
</head>
<body>

<section class="spread spread--cover" style="left:151px;top:5px">
  <svg class="shapes" viewBox="0 0 296 210" preserveAspectRatio="none">
    <defs>
      <linearGradient id="mossTone" x1="0" y1="0" x2="1" y2="1">
        <stop offset="0" stop-color="#5d6a22"/><stop offset=".5" stop-color="#9a9a2c"/><stop offset="1" stop-color="#4f5d20"/>
      </linearGradient>
    </defs>
    <polygon role="img" aria-label="Moosbild in Gelb- und Grüntönen, Draufsicht" points="0,0 276,0 184,210 0,210" fill="url(#mossTone)"/>
  </svg>
  <div class="brand"><span class="brand__mark"></span><span>Wettberg<br>Raumbegrünung</span></div>
</section>

<section class="spread" style="left:457px;top:5px">
  <svg class="shapes" viewBox="0 0 594 210" preserveAspectRatio="none">
    <defs>
      <linearGradient id="cafeTone" x1="0" y1="0" x2="1" y2="0">
        <stop offset="0" stop-color="#8c6d4c"/><stop offset=".5" stop-color="#5f6a2c"/><stop offset="1" stop-color="#6e5436"/>
      </linearGradient>
    </defs>
    <polygon role="img" aria-label="Grünpflanzen am Seitenrand" points="0,0 90,0 0,198" fill="var(--foliage)"/>
    <polygon role="img" aria-label="Café mit Moos-Wandpaneelen, Holztischen und Stühlen" points="191,0 421,0 330,210 97,210" fill="url(#cafeTone)"/>
    <polygon points="421,0 520,0 426,210 330,210" fill="var(--green)"/>
    <polygon role="img" aria-label="Vertikaler Pflanzengarten mit roten Anthurien" points="520,0 587,0 587,210 426,210" fill="#3f6b2e"/>
  </svg>
  <h2 class="heading">Pflege &amp;<br>Wartung</h2>
  <div class="copy copy--justify" style="left:0;top:58px;width:200px">
    <span class="slant-left"></span><span class="slant-right"></span>
    <p>Sie kommen morgens in die Firma, öffnen die Tür zum Büro, setzen sich, und haben bereits eine Grünpflanze vor sich? Hervorragend!</p>
    <p>Gießen, Düngen, Schneiden, Abstauben, Umtopfen: kurzum die Rundumversorgung Ihrer Pflanzen bieten wir Ihnen gerne für Ihren existierenden kleinen Urwald an.</p>
  </div>
  <div class="copy copy--light copy--center" style="left:360px;top:59px;width:100px">
    <p>Cab inus id ut liam et estio. Ipsam ex ex est dolorum faces et as debist, suntota dolo qui ommodia vel istio cus, nest ut aped quaestr underia veliber.</p>
    <p>ovitam hil ide susci dolupiendae vellupt atquam ut atquam etur atius apicius ditat volorporum sitatem ut od qui cus, quia iusae nimetur reperup tassunti nonectur?</p>
  </div>
  <span class="folio" style="left:6px">10</span>
</section>

<section class="spread" style="left:2px;top:220px">
  <svg class="shapes" viewBox="0 0 594 210" preserveAspectRatio="none">
    <defs>
      <linearGradient id="atriumTone" x1="0" y1="0" x2="1" y2="1">
        <stop offset="0" stop-color="#a9ad9a"/><stop offset=".45" stop-color="#4d7c36"/><stop offset="1" stop-color="#3c6a2c"/>
      </linearGradient>
    </defs>
    <polygon role="img" aria-label="Atrium mit Treppe und dicht bepflanztem Beet" points="0,0 435,0 343,210 0,210" fill="url(#atriumTone)"/>
    <polygon points="0,0 70,0 0,160" fill="var(--green-mist)" opacity=".45"/>
    <polygon points="60,150 0,210 0,150" fill="var(--green-pale)" opacity=".4"/>
  </svg>
  <h2 class="heading">Inhalts-<br>verzeichnis</h2>
  <h2 class="heading" style="top:44px">Contents</h2>
  <nav>
    <div class="toc" style="left:453px;top:17px;width:123px"><span>Wer wir sind / About us</span><span class="toc__dots"></span><span>6</span></div>
    <div class="toc" style="left:448px;top:29px;width:128px"><span>XY</span><span class="toc__dots"></span><span>8</span></div>
    <div class="toc" style="left:442px;top:41px;width:134px"><span>XY</span><span class="toc__dots"></span><span>16</span></div>
    <div class="toc" style="left:437px;top:53px;width:139px"><span>XY</span><span class="toc__dots"></span><span>22</span></div>
    <div class="toc" style="left:431px;top:65px;width:145px"><span>XY</span><span class="toc__dots"></span><span>28</span></div>
    <div class="toc" style="left:426px;top:77px;width:150px"><span>XY</span><span class="toc__dots"></span><span>32</span></div>
    <div class="toc" style="left:421px;top:89px;width:155px"><span>XY</span><span class="toc__dots"></span><span>38</span></div>
    <div class="toc" style="left:415px;top:101px;width:161px"><span>XY</span><span class="toc__dots"></span><span>46</span></div>
    <div class="toc" style="left:410px;top:113px;width:166px"><span>XY</span><span class="toc__dots"></span><span>52</span></div>
    <div class="toc" style="left:405px;top:125px;width:171px"><span>XY</span><span class="toc__dots"></span><span>54</span></div>
    <div class="toc" style="left:399px;top:137px;width:177px"><span>XY</span><span class="toc__dots"></span><span>56</span></div>
    <div class="toc" style="left:394px;top:149px;width:182px"><span>XY</span><span class="toc__dots"></span><span>60</span></div>
    <div class="toc" style="left:389px;top:161px;width:187px"><span>XY</span><span class="toc__dots"></span><span>61</span></div>
    <div class="toc" style="left:383px;top:173px;width:193px"><span>XY</span><span class="toc__dots"></span><span>62</span></div>
    <div class="toc" style="left:378px;top:185px;width:198px"><span>XY</span><span class="toc__dots"></span><span>64</span></div>
  </nav>
</section>

<section class="spread" style="left:601px;top:220px">
  <svg class="shapes" viewBox="0 0 594 210" preserveAspectRatio="none">
    <defs>
      <linearGradient id="officeTone" x1="0" y1="0" x2="0" y2="1">
        <stop offset="0" stop-color="#9a8f72"/><stop offset=".45" stop-color="#d8cf86"/><stop offset="1" stop-color="#6f7378"/>
      </linearGradient>
    </defs>
    <polygon points="0,0 90,0 39,210 0,210" fill="var(--green-dark)"/>
    <polygon points="0,0 55,0 0,130" fill="var(--green)" opacity=".6"/>
    <polygon points="0,150 39,210 0,210" fill="#8d9a89"/>
    <polygon role="img" aria-label="Büroflur mit gelben Wänden und einem gepflanzten Baum im Bodenbeet" points="90,0 435,0 343,210 39,210" fill="url(#officeTone)"/>
  </svg>
  <h2 class="heading">Neubegrünung<br>&amp; Lieferung</h2>
  <div class="copy copy--center" style="left:398px;top:54px;width:190px">
    <p>Wir kümmern uns mit unserem Team gerne um Ihre bestehenden Pflanzen. Unsere ältesten Schützlinge wurden in den 1970ern gepflanzt und erfreuen sich auch in ihrem bald 50. Lebensjahr bester Gesundheit.</p>
    <p>Unsere kleinsten Grünen sind kaum höher als ein Steckling, unsere Größten strecken sich in Eingangshallen bis 5 Meter in die Höhe. Manche unserer Kunden erfreuen sich in ihrer Hauptverwaltung an 2000 Pflanzen und das typische Startup ist stolz auf die ersten 5 grünen Mitbewohner.</p>
    <p>Wir sind spezialisiert auf die Innenraumbegrünung, die wir mögen, können und lieben. Vielleicht auch bald in Ihren Räumlichkeiten?</p>
  </div>
  <span class="caption" style="left:355px;top:192px">Einer unserer ältesten: Gepflanzt 1978, stolze 41 Jahre alt</span>
  <span class="folio" style="left:6px;color:#fff">6</span>
  <span class="folio" style="right:8px">7</span>
</section>

<section class="spread" style="left:2px;top:434px">
  <svg class="shapes" viewBox="0 0 594 210" preserveAspectRatio="none">
    <polygon points="0,0 435,0 343,210 0,210" fill="var(--green)"/>
    <polygon points="0,0 89,0 0,160" fill="var(--green-pale)"/>
    <polygon points="0,158 43,210 0,210" fill="var(--green-pale)"/>
  </svg>
  <div class="fold"></div>
  <h2 class="heading heading--green" style="font-weight:500">Wer wir sind<br>About us</h2>
  <figure class="member" style="left:64px;top:12px"><div class="member__photo" role="img" aria-label="Porträt Konrad Wettberg"></div><figcaption class="member__name">Konrad Wettberg</figcaption></figure>
  <figure class="member" style="left:155px;top:12px"><div class="member__photo" role="img" aria-label="Porträt Helga Wettberg"></div><figcaption class="member__name">Helga Wettberg</figcaption></figure>
  <figure class="member" style="left:18px;top:109px"><div class="member__photo" role="img" aria-label="Porträt Jonas Wettberg"></div><figcaption class="member__name">Jonas Wettberg</figcaption></figure>
  <figure class="member" style="left:109px;top:109px"><div class="member__photo" role="img" aria-label="Porträt Lukas Wettberg"></div><figcaption class="member__name">Lukas Wettberg</figcaption></figure>
  <figure class="member" style="left:201px;top:109px"><div class="member__photo" role="img" aria-label="Porträt Mara Wettberg"></div><figcaption class="member__name">Mara Wettberg</figcaption></figure>
  <div class="copy copy--justify" style="left:410px;top:80px;width:166px;font-size:4.4px">
    <p>Wir sind Wettberg Raumbegrünung, das Familienunternehmen in der Raumbegrünung und Hydrokultur. In unserer tagtäglichen Arbeit liefern und pflegen wir Pflanzen in Büros, Versicherungen, Banken, Callcentern, Schulen, Schwimmbädern und Behörden.</p>
  </div>
  <div class="badge" role="img" aria-label="Zertifikat"></div>
  <span class="folio" style="left:7px">4</span>
  <span class="folio" style="right:8px">5</span>
</section>

<section class="spread" style="left:601px;top:434px">
  <svg class="shapes" viewBox="0 0 594 210" preserveAspectRatio="none">
    <polygon points="0,0 44,0 0,100" fill="var(--green-mist)"/>
    <polygon points="188,0 332,0 241,210 97,210" fill="var(--green)"/>
    <polygon points="332,0 426,0 332,210 241,210" fill="var(--anthracite)"/>
  </svg>
  <h2 class="heading heading--small">Neubegrünung<br>&amp; Lieferung</h2>
  <div class="photo" role="img" aria-label="Große Palme in Edelstahlkübel im Foyer" style="left:35px;top:11px;width:129px;height:185px;background:linear-gradient(180deg,#c9c2b4,#587a5a 45%,#a8a6a0)"></div>
  <div class="copy copy--light" style="left:170px;top:61px;width:107px">
    <p>Sie kommen morgens in die Firma, öffnen die Tür zum Büro, setzen sich, und starren erst einmal auf eine kahle Wand? Zeit, etwas Farbe in Ihr Büro zu bringen. Und am besten natürlich grün! Pflanzen im Büro lockern die Arbeitsatmosphäre auf und sorgen dafür, dass sich alle wohlfühlen. Wir kümmern uns um die Neubegrünung Ihrer Büroräumlichkeiten.</p>
  </div>
  <span class="caption" style="left:170px;top:193px;color:#fff">Einer unserer größten: 5 Meter</span>
  <div class="copy" style="left:423px;top:26px;width:164px">
    <p>Dendaeprepti voluptatum facimusapis doluptio id quibus doloreperio es dolenest pro blaudicius etur aute dit modignis nos eaquas sitius eum ut aut dic to doluptae. Ita doloruntem raepreris ad ex earumquas debit pro maximusam volorep edignat ectam, sint officiae consed ut voluptate post, con none et quae. Moloreremodi tem sed mi, sitatati blaccatem nisin.</p>
  </div>
  <div class="photo" role="img" aria-label="Treppenhaus mit üppig bepflanztem Hochbeet" style="left:348px;top:67px;width:228px;height:128px;background:linear-gradient(135deg,#d4d1c8,#5b8a42 55%,#3f6a2e)"></div>
  <span class="folio" style="left:7px">8</span>
  <span class="folio" style="right:8px">9</span>
</section>

</body>
</html>
```